Assessment Flyer

We are looking for a marketing flyer for our business. We are a psychology practice that has recently expanded our assessment team and availability. We need a flyer to fax to GP's and other referrers. We have previously sent out rather basic flyers as it was more of a courtesy update about our practice rather than a marketing tool. We have recently created a brochure just focusing on assessments which can be used as a guide for the flyer. We want to update them about our expansion, highlight the assessments we do, introduce our new psychologists, and touch on availability.

```html
<!DOCTYPE html>
<html lang="en">
<head>
<meta charset="utf-8">
<title>Assessment Service Flyer</title>
<link href="https://fonts.googleapis.com/css2?family=Poppins:wght@400;500;600&family=Yesteryear&display=swap" rel="stylesheet">
<style>
  :root{
    --backdrop:#7b7b7b;
    --paper:#ffffff;
    --teal:#0aa99b;
    --teal-deep:#079c91;
    --green:#7cc242;
    --green-mid:#3fb76a;
    --text:#4a4a4a;
    --text-strong:#3a3a3a;
    --white:#ffffff;
  }
  *{margin:0;padding:0;box-sizing:border-box}
  html,body{width:1200px;height:1200px;overflow:hidden;background:var(--backdrop)}
  body{font-family:"Poppins",sans-serif;color:var(--text);position:relative}
  .flyer{position:absolute;left:260px;top:120px;width:680px;height:960px;background:var(--paper);overflow:hidden}
  .hero{position:absolute;left:0;top:0;width:680px;height:342px;
    background:linear-gradient(180deg,#f4b07a 0%,#e9a27a 22%,#8a7a5c 42%,#5d6a36 62%,#3c4a22 82%,#2c3419 100%)}
  .hero-shade{position:absolute;inset:0;background:linear-gradient(180deg,rgba(0,0,0,0) 40%,rgba(0,0,0,.35) 100%)}
  .brand-tab{position:absolute;left:0;top:0;width:300px;height:92px;background:var(--paper);
    clip-path:polygon(0 0,100% 0,88% 78%,84% 92%,78% 100%,0 100%)}
  .brand{position:absolute;left:34px;top:30px;display:flex;align-items:center;gap:10px;
    font-size:19px;font-weight:600;color:var(--teal)}
  .brand-dot{width:30px;height:30px;border-radius:50%;background:var(--teal)}
  .hero-title{position:absolute;left:0;width:680px;top:158px;text-align:center;
    font-family:"Yesteryear",cursive;font-size:66px;color:var(--white);line-height:1;text-shadow:0 2px 6px rgba(0,0,0,.35)}
  .hero-intro{position:absolute;left:44px;width:592px;top:248px;text-align:center;
    font-size:13.4px;line-height:16.6px;color:var(--white);font-weight:500}
  .section-pill{position:absolute;left:43px;height:37px;border-radius:19px;
    background:linear-gradient(90deg,var(--green) 0%,var(--green-mid) 45%,var(--teal) 100%);
    display:flex;align-items:center;padding-left:5px;gap:9px}
  .pill-icon{width:28px;height:28px;border-radius:50%;background:var(--white);display:flex;align-items:center;justify-content:center}
  .pill-title{font-family:"Yesteryear",cursive;font-size:27px;color:var(--white);line-height:1}
  .pill-assess{top:324px;width:292px}
  .pill-team{top:497px;width:292px}
  .pill-avail{top:738px;width:190px}
  .assessments{position:absolute;left:30px;top:374px;display:flex}
  .assessment{width:83px;display:flex;flex-direction:column;align-items:center;text-align:center;
    font-size:10px;line-height:12px;font-weight:500;color:var(--text)}
  .assessment-ring{width:58px;height:58px;border-radius:50%;border:2px solid var(--green-mid);
    display:flex;align-items:center;justify-content:center;margin-bottom:6px}
  .assessment-art{width:38px;height:38px;border-radius:50%;background:linear-gradient(135deg,#d7f0c2,#bfe9dc)}
  .team{position:absolute;left:50px;top:543px;list-style:none;font-size:14.2px;line-height:19.6px}
  .team li{position:relative;padding-left:18px;color:var(--text)}
  .team li::before{content:"";position:absolute;left:0;top:6px;width:9px;height:9px;
    background:var(--green);border-radius:0 70% 0 70%}
  .team strong{font-weight:600;color:var(--text-strong)}
  .availability{position:absolute;left:45px;top:780px;font-size:14.2px}
  .availability strong{font-weight:600;color:var(--text-strong)}
  .footer-wave{position:absolute;left:0;top:0}
  .contact{position:absolute;color:var(--white);font-size:12.6px;line-height:15.6px}
  .address{left:52px;display:flex;align-items:center;gap:10px}
  .address-1{top:866px}
  .address-2{top:913px}
  .round-icon{width:28px;height:28px;border-radius:50%;border:1.5px solid var(--white);display:flex;align-items:center;justify-content:center;flex:none}
  .phones{left:288px;top:866px;display:flex;align-items:center;gap:6px;font-size:19px;font-weight:600}
  .phones .round-icon{width:26px;height:26px}
  .phones .gap{width:8px}
  .divider{position:absolute;left:290px;top:903px;width:370px;height:1px;background:rgba(255,255,255,.6)}
  .online{left:290px;top:917px}
  .online div{display:flex;align-items:center;gap:7px}
</style>
</head>
<body>
  <main class="flyer">
    <div class="hero" role="img" aria-label="Photograph of rolling farmland at sunset with trees framing the view"><div class="hero-shade"></div></div>
    <div class="brand-tab"></div>
    <div class="brand"><span class="brand-dot"></span>Brightwater Psychology &amp; Wellness</div>
    <h1 class="hero-title">Assessment Service</h1>
    <p class="hero-intro">Brightwater Psychology and Wellness is excited to announce the expansion of our assessment team. As the need for assessment services has grown, we have worked diligently to expand our team with highly skilled psychologists to support these needs.</p>

    <div class="section-pill pill-assess">
      <span class="pill-icon"><svg width="16" height="16" viewBox="0 0 16 16"><rect x="3" y="2" width="10" height="12" rx="1.5" fill="none" stroke="#3fb76a" stroke-width="1.4"/><path d="M5.5 6h5M5.5 9h5M5.5 12h3" stroke="#3fb76a" stroke-width="1.2"/></svg></span>
      <span class="pill-title">Available Assessments</span>
    </div>
    <div class="assessments">
      <div class="assessment"><span class="assessment-ring"><span class="assessment-art" role="img" aria-label="Icon of books and a graduation cap"></span></span>Educational<br>Assessment</div>
      <div class="assessment"><span class="assessment-ring"><span class="assessment-art" role="img" aria-label="Icon of a person with focus symbol"></span></span>ADHD:<br>Children and<br>Adults</div>
      <div class="assessment"><span class="assessment-ring"><span class="assessment-art" role="img" aria-label="Icon of a calendar with puzzle piece"></span></span>Autism:<br>Children and<br>Adults</div>
      <div class="assessment"><span class="assessment-ring"><span class="assessment-art" role="img" aria-label="Icon of a person in a wheelchair"></span></span>Intellectual<br>Disability</div>
      <div class="assessment"><span class="assessment-ring"><span class="assessment-art" role="img" aria-label="Icon of a gift box"></span></span>Giftedness</div>
    </div>

    <div class="section-pill pill-team">
      <span class="pill-icon"><svg width="16" height="16" viewBox="0 0 16 16"><circle cx="8" cy="5" r="2.3" fill="none" stroke="#3fb76a" stroke-width="1.3"/><path d="M3.5 13c.6-3 2.4-4.3 4.5-4.3s3.9 1.3 4.5 4.3" fill="none" stroke="#3fb76a" stroke-width="1.3"/></svg></span>
      <span class="pill-title">Meet the Assessment Team</span>
    </div>
    <ul class="team">
      <li><strong>Dr Maren Holloway:</strong> Clinical Director</li>
      <li><strong>Dr Clare Whitfield:</strong> Registered Psychologist</li>
      <li><strong>Dr Ingrid Solvay:</strong> Counselling Psychologist</li>
      <li><strong>Lena Marchetti:</strong> Registered Psychologist</li>
      <li><strong>Gianna Rossetti:</strong> Registered Psychologist</li>
      <li><strong>Adriana Montalvo Whitcombe:</strong><br>Registered Psychologist</li>
      <li><strong>Sophie Ardley:</strong> Provisional Psychologist</li>
      <li><strong>Amy Pritchard:</strong> Provisional Psychologist</li>
    </ul>

    <div class="section-pill pill-avail">
      <span class="pill-icon"><svg width="16" height="16" viewBox="0 0 16 16"><rect x="2" y="3" width="12" height="11" rx="1.5" fill="none" stroke="#3fb76a" stroke-width="1.3"/><path d="M2 6.5h12M5 1.5v3M11 1.5v3" stroke="#3fb76a" stroke-width="1.3"/></svg></span>
      <span class="pill-title">Availability</span>
    </div>
    <p class="availability">Appointments available from <strong>early March 2024</strong></p>

    <svg class="footer-wave" width="680" height="960" viewBox="0 0 680 960" aria-hidden="true">
      <defs>
        <linearGradient id="waveLine" x1="0" x2="1" y1="0" y2="0">
          <stop offset="0" stop-color="#3fb76a"/><stop offset="1" stop-color="#9ed35b"/>
        </linearGradient>
      </defs>
      <path d="M0 858 C120 830 260 840 380 822 C460 810 520 770 580 770 C630 770 660 790 680 780 L680 960 L0 960 Z" fill="var(--teal)"/>
      <path d="M0 858 C90 836 200 832 300 836 C380 840 440 826 530 808" fill="none" stroke="url(#waveLine)" stroke-width="4"/>
    </svg>

    <div class="contact address address-1">
      <span class="round-icon"><svg width="12" height="12" viewBox="0 0 12 12"><path d="M11 1 1 5.5l4.5 1 1 4.5z" fill="#fff"/></svg></span>
      <span>114 Esplanade Road<br>Seacliff Bay, SA, 5049</span>
    </div>
    <div class="contact address address-2">
      <span class="round-icon"><svg width="12" height="12" viewBox="0 0 12 12"><path d="M11 1 1 5.5l4.5 1 1 4.5z" fill="#fff"/></svg></span>
      <span>3/27 Harbour Terrace<br>Seacliff Bay SA 5049</span>
    </div>
    <div class="contact phones">
      <span class="round-icon"><svg width="13" height="13" viewBox="0 0 14 14"><path d="M3 1.5 5 1l1.2 3-1.4 1a7 7 0 0 0 4.2 4.2l1-1.4 3 1.2-.5 2A2 2 0 0 1 10.5 13C5.6 12.6 1.4 8.4 1 3.5A2 2 0 0 1 3 1.5z" fill="#fff"/></svg></span>
      <span>(08) 7000 1234</span>
      <span class="gap"></span>
      <span class="round-icon"><svg width="13" height="13" viewBox="0 0 14 14"><rect x="2" y="5" width="10" height="7" rx="1" fill="none" stroke="#fff" stroke-width="1.3"/><rect x="4" y="1.5" width="6" height="3.5" fill="none" stroke="#fff" stroke-width="1.2"/><path d="M4 8h2M8 8h2M4 10h2M8 10h2" stroke="#fff"/></svg></span>
      <span>(08) 6000 5678</span>
    </div>
    <div class="divider"></div>
    <div class="contact online">
      <div><svg width="12" height="10" viewBox="0 0 12 10"><rect x=".6" y=".6" width="10.8" height="8.8" fill="none" stroke="#fff" stroke-width="1"/><path d="M.6.6 6 5.5 11.4.6" fill="none" stroke="#fff" stroke-width="1"/></svg>reception@brightwaterpsychology.com.au</div>
      <div><svg width="12" height="12" viewBox="0 0 12 12"><circle cx="6" cy="6" r="5.2" fill="none" stroke="#fff"/><ellipse cx="6" cy="6" rx="2.3" ry="5.2" fill="none" stroke="#fff"/><path d="M1 6h10" stroke="#fff"/></svg>www.brightwaterpsychology.com.au</div>
    </div>
  </main>
</body>
</html>
```